Building company buisness cards

We are looking for a sharp modern new look for our business cards.
We are a New Zealand based company that specialises in house and land packages.
We have attached a photo of the current logo and would like to see if it can be improved somehow if needed.
We are open to any colours but we have chosen green at this stage.
Feel free to change the font and make the logo smarter looking.
Play with the colours and see what looks best.

We want a card that looks so good know one will want to throw it away!

Target Market(s)

Home buyers

Industry/Entity Type

Building

Contact Information for Business Card

Derek Tolvane
0217394062
dtolvane@quillmarkhomesteads.co.nz
quillmarkhomesteads.co.nz

Font styles to use
Serif
Sans Serif

Colors

Designer to choose colors to be used in the design.

Requirements
Must have
• Logo and company name on one side, details on the other side
Nice to have
• Color codes for the original green are HEX #4a8028, RGB(74,128,40), CMYK(42,0,69,50)
• Round corners, Raised and/or spot UV

```html
<!DOCTYPE html>
<html lang="en">
<head>
<meta charset="utf-8">
<title>Quillmark Homesteads – Business Card</title>
<link rel="stylesheet" href="https://fonts.googleapis.com/css2?family=Montserrat:wght@700;800&family=Roboto:wght@400&display=swap">
<style>
  :root {
    --brand-green: #4a8028;
    --stripe-grey: #6b6b6b;
    --text-grey: #555555;
    --card-white: #ffffff;
    --stage: #e9ebe8;
  }
  * { margin: 0; padding: 0; box-sizing: border-box; }
  html, body { width: 1200px; height: 900px; overflow: hidden; }
  body {
    background: var(--stage);
    display: flex;
    flex-direction: column;
    align-items: center;
    justify-content: center;
    gap: 52px;
    font-family: "Roboto", Arial, sans-serif;
  }
  .card {
    position: relative;
    width: 620px;
    height: 354px;
    border-radius: 22px;
    overflow: hidden;
    box-shadow: 0 6px 18px rgba(0,0,0,0.12);
  }
  /* Front */
  .card--front {
    background: var(--brand-green);
    color: var(--card-white);
    display: flex;
    flex-direction: column;
    align-items: center;
    justify-content: center;
  }
  .brand {
    font-family: "Montserrat", Arial, sans-serif;
    font-weight: 800;
    line-height: 0.95;
    text-align: center;
    letter-spacing: -0.5px;
  }
  .brand__mark {
    display: block;
    width: 30px;
    height: 30px;
    border-radius: 50%;
    background: currentColor;
    margin: 0 auto 14px;
  }
  .card--front .brand { font-size: 50px; }
  .card--front .brand__top { font-size: 34px; display: block; }
  .front__web {
    margin-top: 36px;
    font-size: 14px;
    letter-spacing: 0.6px;
  }
  /* Back */
  .card--back { background: var(--card-white); }
  .back__wave { position: absolute; inset: 0; }
  .card--back .brand {
    position: absolute;
    left: 46px;
    top: 58px;
    color: var(--brand-green);
    font-size: 32px;
    text-align: left;
  }
  .card--back .brand__top { font-size: 22px; display: block; padding-left: 44px; }
  .card--back .brand__mark { width: 18px; height: 18px; margin: 0 0 8px 96px; }
  .back__rule {
    position: absolute;
    left: 46px;
    right: 46px;
    top: 226px;
    height: 1.5px;
    background: var(--brand-green);
  }
  .contact {
    position: absolute;
    left: 46px;
    top: 240px;
    list-style: none;
    font-size: 14px;
    color: var(--text-grey);
    line-height: 21px;
  }
  .contact li { display: flex; align-items: center; gap: 8px; }
  .contact svg { width: 11px; height: 11px; flex: none; }
  .contact__web span { color: var(--brand-green); }
  .person {
    position: absolute;
    right: 40px;
    top: 162px;
    text-align: right;
  }
  .person__name {
    font-family: "Montserrat", Arial, sans-serif;
    font-weight: 700;
    font-size: 27px;
    color: var(--brand-green);
  }
  .person__role {
    font-size: 15px;
    color: var(--text-grey);
    margin-top: 1px;
  }
</style>
</head>
<body>

  <section class="card card--front" aria-label="Card front">
    <div class="brand">
      <span class="brand__mark"></span>
      <span class="brand__top">quillmark</span>
      homesteads.
    </div>
    <div class="front__web">www.quillmarkhomesteads.co.nz</div>
  </section>

  <section class="card card--back" aria-label="Card back">
    <svg class="back__wave" viewBox="0 0 620 354" aria-hidden="true">
      <path d="M0 0 H620 V150 C560 152 500 138 430 100 C340 50 220 18 0 30 Z" fill="#4a8028"/>
      <path d="M0 40 C220 28 340 62 430 112 C500 150 560 163 620 162" fill="none" stroke="#ffffff" stroke-width="6"/>
      <path d="M0 44 C220 32 340 66 430 116 C500 154 560 167 620 166" fill="none" stroke="#6b6b6b" stroke-width="9"/>
    </svg>

    <div class="brand">
      <span class="brand__mark"></span>
      <span class="brand__top">quillmark</span>
      homesteads.
    </div>

    <div class="person">
      <div class="person__name">Derek Tolvane</div>
      <div class="person__role">Founder</div>
    </div>

    <div class="back__rule"></div>

    <ul class="contact">
      <li>
        <svg viewBox="0 0 12 12"><path d="M3 1 L5 3.5 L4 5 C4.8 6.6 5.6 7.4 7 8 L8.5 7 L11 9 L9.6 11 C5 10.5 1.5 7 1 2.4 Z" fill="#4a8028"/></svg>
        0217394062
      </li>
      <li>
        <svg viewBox="0 0 12 12"><rect x="1" y="2.5" width="10" height="7" fill="none" stroke="#4a8028" stroke-width="1.2"/><path d="M1 2.5 L6 6.5 L11 2.5" fill="none" stroke="#4a8028" stroke-width="1.2"/></svg>
        dtolvane@quillmarkhomesteads.co.nz
      </li>
      <li class="contact__web">
        <svg viewBox="0 0 12 12"><circle cx="6" cy="6" r="5" fill="none" stroke="#4a8028" stroke-width="1.2"/><ellipse cx="6" cy="6" rx="2" ry="5" fill="none" stroke="#4a8028" stroke-width="1"/><path d="M1 6 H11" stroke="#4a8028" stroke-width="1"/></svg>
        <p>www.<span>quillmarkhomesteads</span>.co.nz</p>
      </li>
    </ul>
  </section>

</body>
</html>
```